Website for a Psychologist in Private Practice

I need a cool web design for my website: www.drkalvoric.com. I would like it to look professional. Keep all the current content and add: Space for video; radio spots (see Silver Cedar Tunes Logo below for those); Quick Inquiry; Friendora link; 5 star rating on Rivo; a map; reviews from former patients. I am open to suggestions.

Target Market(s)

Those seeking individual and marital counseling.

Industry/Entity Type

Mental Health

Number of Pages Required

1 page

Font styles to use
Sans Serif
Other font styles liked:
• I'm open but no hard to read script

Requirements
Must have
• All the content on my home page with link for video and radio spots. List services and degrees and expertices (pics not necessary).
Nice to have
• A video of me and radio conversations (logo of Silver Cedar Tunes radio attached).
Should not have
• Cartoons, comedy, etc.... I don't need pictures of services (marital, depression, etc...) Just list those.

```html
<!DOCTYPE html>
<html lang="en">
<head>
<meta charset="utf-8">
<title>Dr. Marla J. Kalvoric – Psychologist</title>
<link href="https://fonts.googleapis.com/css2?family=Signika:wght@400;600&family=Arimo:ital,wght@0,400;0,700;1,400;1,700&display=swap" rel="stylesheet">
<style>
:root{
  --blue:#2a7fc6;
  --blue-dark:#1f6aa8;
  --title-blue:#2f86c4;
  --ink:#222;
  --white:#fff;
  --panel:rgba(22,70,80,.55);
  --band:rgba(10,40,48,.55);
  --review:rgba(70,62,55,.72);
  --footer:#2a2828;
  --footer-text:#e6e6e6;
  --accent-orange:#f0a040;
  --field:rgba(60,66,70,.85);
}
*{box-sizing:border-box;margin:0;padding:0}
html,body{width:743px;height:1200px;overflow:hidden}
body{position:relative;background:#fff;font-family:"Arimo",Arial,sans-serif;color:var(--ink)}
.abs{position:absolute}
.head-font{font-family:"Signika",Arial,sans-serif}

/* header */
.topline{left:0;top:0;width:743px;height:2px;background:var(--blue)}
.brand{left:83px;top:16px;font:400 24px "Signika",sans-serif;color:var(--title-blue)}
.license{left:445px;top:33px;font:400 8.5px "Arimo",sans-serif;color:#333}
.call-icon{left:551px;top:19px}
.call-label{left:576px;top:19px;font:400 9.5px "Arimo",sans-serif;color:#222}
.call-number{left:578px;top:30px;font:400 14px "Signika",sans-serif;color:var(--title-blue)}

/* nav */
.nav{left:0;top:58px;width:743px;height:28px;background:var(--blue)}
.nav a{position:absolute;top:8px;font:400 10px "Signika",sans-serif;color:#fff;text-decoration:none}
.nav a.active{color:#111}
.nav .sep{position:absolute;top:0;width:1px;height:28px;background:rgba(255,255,255,.25)}
.follow{position:absolute;top:9px;font:400 8px "Signika",sans-serif;color:#fff}
.social{position:absolute;top:8px;font:400 8.5px "Signika",sans-serif;color:#fff;display:flex;align-items:center;gap:3px}
.social i{display:inline-block;width:9px;height:9px;border-radius:50%;background:#fff}

/* hero */
.hero{left:0;top:86px;width:743px;height:272px;background:radial-gradient(ellipse at 60% 40%,#b5b5b5 0%,#8e8e8e 45%,#555 100%)}
.hero-piece{left:250px;top:20px;width:200px;height:230px;border-radius:30px;background:radial-gradient(circle at 50% 40%,#d8b04a,#8a6415 75%);opacity:.9}
.hero-line{left:82px;top:178px;font:400 19px/26px "Signika",sans-serif;color:#fff}
.arrow{top:210px;width:22px;height:22px;background:rgba(60,60,60,.8);border:1px solid #bbb}
.arrow svg{display:block;margin:5px}

/* main */
.beach{left:0;top:358px;width:743px;height:664px;background:linear-gradient(180deg,#7fa6c8 0%,#3f8fb0 20%,#1f8c9c 45%,#5fb1b4 62%,#c9c1a6 78%,#b7a68c 100%)}
.panel{left:82px;top:358px;width:581px;height:484px;background:var(--panel)}
.col-title{font:400 14px/15px "Signika",sans-serif;color:#fff}
.rule{height:2px;background:rgba(255,255,255,.45)}
.rule b{display:block;height:2px;background:var(--blue);width:60%;margin-left:auto}
.about-text{left:88px;top:427px;width:175px;font:400 8.4px/13px "Arimo",sans-serif;color:#fff}
.link{color:#fff;text-decoration:underline;font:400 9px "Arimo",sans-serif}
.portrait{border-radius:50%;background:linear-gradient(160deg,#c8b287,#6d7d96);border:2px solid #fff}
.exp-name{left:357px;top:440px;font:400 13.5px/18px "Signika",sans-serif;color:#fff}
.exp-list{left:291px;top:488px;list-style:none;font:400 8.5px/13px "Arimo",sans-serif;color:#fff}
.exp-list li::before{content:"✓";margin-right:4px}
.radio-box{left:481px;top:428px;width:175px;height:105px;background:rgba(225,228,230,.85);border:1px solid #ccc;padding:6px 9px}
.radio-box p{font:400 8.4px/13px "Arimo",sans-serif;color:#555}
.radio-box .qm{color:#999;font:700 14px/8px Georgia,serif}
.radio-box .who{text-align:right;font:400 8px Georgia,serif;color:#555;margin-top:4px}

.degrees{left:82px;top:579px;width:581px;height:48px;background:var(--band)}
.deg-title{left:147px;top:595px;font:400 13px "Signika",sans-serif;color:#fff}
.deg-item{font:400 8.5px "Arimo",sans-serif;color:#fff}

.section-title{font:400 14px "Signika",sans-serif;color:#fff}
.video{left:88px;top:677px;width:181px;height:139px;border:2px solid var(--blue);background:linear-gradient(150deg,#d7c49a 0%,#9aa8b7 55%,#4a6a8c 100%)}
.play{left:159px;top:736px}
.inq-desc{left:293px;top:681px;font:400 7.5px "Arimo",sans-serif;color:#fff}
.field{left:293px;width:172px;height:18px;background:var(--field);font:400 7.5px "Arimo",sans-serif;color:#cfd3d6;padding:5px 7px}
.submit{left:293px;top:797px;width:68px;height:19px;background:var(--blue);color:#fff;font:700 9px "Arimo",sans-serif;text-align:center;line-height:19px}
.poster{left:485px;top:652px;width:163px;height:163px;background:linear-gradient(160deg,#d4305e 0%,#b5706c 30%,#8a6a5e 65%,#c03560 100%)}

.reviews{left:82px;top:842px;width:581px;height:180px;background:var(--review)}
.rev-title{left:82px;top:860px;width:581px;text-align:center;font:400 14px "Signika",sans-serif;color:#fff}
.rev-rule{left:277px;top:881px;width:188px;height:1px;background:rgba(255,255,255,.7)}
.rev-rule b{position:absolute;left:73px;top:-1px;width:44px;height:3px;background:var(--blue)}
.rev-photo{left:88px;top:896px;width:72px;height:72px}
.rev-quote{left:172px;top:900px;width:478px;font:italic 400 8.2px/14.6px "Arimo",sans-serif;color:#fff}
.rev-quote .qm{font:700 22px/8px Georgia,serif;color:#9a928a;margin-right:4px;vertical-align:-6px}
.rev-who{left:173px;top:970px;font:italic 700 8px "Arimo",sans-serif;color:#fff}
.rev-more{right:90px;top:981px;font:400 8px "Arimo",sans-serif;color:#fff}

/* footer */
.footer{left:0;top:1022px;width:743px;height:152px;background:var(--footer)}
.f-title{font:400 9.5px "Signika",sans-serif;color:#fff;padding-bottom:4px;border-bottom:1px dashed #777}
.f-links{left:88px;top:1063px;list-style:none;font:400 8px/13.7px "Arimo",sans-serif;color:var(--footer-text)}
.f-links li:first-child{color:var(--accent-orange)}
.badge-a{left:212px;top:1061px;width:127px;height:50px;background:#fff;border:2px solid #3b8fcf}
.badge-b{left:212px;top:1114px;width:127px;height:48px;background:#8caa3e;border:2px solid #3b8fcf}
.c-row{font:400 8px/11.5px "Arimo",sans-serif;color:var(--footer-text)}
.c-row b{display:inline-block;width:18px;font-weight:400}
.rating{left:594px;top:1058px;width:51px;height:50px;border-radius:7px;background:#c8231f;border:2px solid #e4e4e4}
.share{left:591px;top:1121px;width:57px;height:18px;background:#3f67a8;border:1px solid #6f8fc2;color:#fff;font:400 7.5px "Arimo",sans-serif;line-height:16px;text-align:center}
.bottom{left:0;top:1174px;width:743px;height:26px;background:var(--blue);color:#fff;font:400 8px "Arimo",sans-serif;text-align:center;line-height:26px}
</style>
</head>
<body>

<header>
  <div class="abs topline"></div>
  <div class="abs brand">Dr. Marla J. Kalvoric</div>
  <div class="abs license">California # PSY20581</div>
  <svg class="abs call-icon" width="20" height="20" viewBox="0 0 20 20" aria-hidden="true">
    <circle cx="10" cy="10" r="8.5" fill="none" stroke="#2f86c4" stroke-width="1.3"/>
    <path d="M7 5.5c-1 1-1 3 .5 5.5s3.5 4 5 4l1-1.3-2-1.6-1 .8c-1-.6-2-1.9-2.4-3l.9-.9-1-2.2z" fill="#2f86c4"/>
  </svg>
  <div class="abs call-label">Call Us Today</div>
  <div class="abs call-number">949-555-0182</div>
</header>

<nav class="abs nav">
  <a class="active" style="left:88px">Home</a>
  <a style="left:135px">About Me</a>
  <span class="sep" style="left:187px"></span>
  <a style="left:198px">Sessions</a>
  <span class="sep" style="left:248px"></span>
  <a style="left:259px">Resources</a>
  <span class="sep" style="left:317px"></span>
  <a style="left:328px">BIO</a>
  <span class="sep" style="left:354px"></span>
  <a style="left:365px">Customer Reviews</a>
  <span class="sep" style="left:458px"></span>
  <a style="left:471px">Contact Us</a>
  <span class="follow" style="left:545px">Follow Us On</span>
  <span class="social" style="left:603px"><i></i>Friendora</span>
  <span class="social" style="left:656px"><i></i>Chirpline</span>
</nav>

<section>
  <div class="abs hero" role="img" aria-label="Silver puzzle pieces with one gold piece bearing the practice name"></div>
  <div class="abs hero-line">The Best way to<br>Conquer a problem<br>is to FACE it</div>
  <div class="abs arrow" style="left:5px"><svg width="10" height="10" viewBox="0 0 10 10"><path d="M6.5 2 3.5 5l3 3" fill="none" stroke="#fff" stroke-width="1.6"/></svg></div>
  <div class="abs arrow" style="left:713px"><svg width="10" height="10" viewBox="0 0 10 10"><path d="M3.5 2l3 3-3 3" fill="none" stroke="#fff" stroke-width="1.6"/></svg></div>
</section>

<main>
  <div class="abs beach" role="img" aria-label="Tropical beach with turquoise sea and sand"></div>
  <div class="abs panel"></div>

  <div class="abs col-title" style="left:90px;top:382px">About<br>Dr. Marla J. Kalvoric</div>
  <div class="abs rule" style="left:88px;top:415px;width:173px"><b></b></div>
  <p class="abs about-text">While I acknowledge the importance of my education, I also appreciate the role my experiences have played in allowing me to relate so well to others. Allow me to share those I feel are most relevant with you. I survived an abusive childhood that my mother &amp; sister unfortunately did not. &amp; it was my grief &amp; desire to become stronger than my past that led me to counseling.....</p>
  <a class="abs link" style="left:88px;top:547px">Read More</a>

  <div class="abs col-title" style="left:288px;top:382px">My<br>Expertise</div>
  <div class="abs rule" style="left:288px;top:415px;width:173px"><b></b></div>
  <div class="abs portrait" style="left:285px;top:422px;width:65px;height:65px" role="img" aria-label="Portrait of Dr. Kalvoric"></div>
  <div class="abs exp-name">Dr. Marla J.<br>Kalvoric</div>
  <ul class="abs exp-list">
    <li>Dating, Marriage,</li>
    <li>Parenting &amp; Professional Relationships</li>
    <li>Depression &amp; Anxiety Issues</li>
    <li>Personality Disorders</li>
    <li>Life Management</li>
  </ul>

  <div class="abs col-title" style="left:481px;top:382px">Radio<br>Conversations</div>
  <div class="abs rule" style="left:481px;top:415px;width:174px"><b></b></div>
  <div class="abs radio-box">
    <p><span class="qm">“</span> Lorem ipsum dolor sit ae onsectetuer adipiscing elit, sed diam nonummy nibh euis tincidunt ut laoreetlore gna aliquam erat olutpat. Ut wisi enim adinim veniam, quis strud xerci tation ullamrper suscipit lobortis sl ut al lorem.</p>
    <p class="who">Nora Pell</p>
  </div>
  <a class="abs link" style="left:481px;top:541px">View All</a>

  <div class="abs degrees"></div>
  <div class="abs deg-title">My Degrees</div>
  <svg class="abs" style="left:229px;top:587px" width="10" height="34" viewBox="0 0 10 34" aria-hidden="true"><path d="M2 1q5 0 5 8t2 8q-2 0-2 8t-5 8" fill="none" stroke="#bbb" stroke-width="1.2"/></svg>
  <div class="abs deg-item" style="left:252px;top:591px">Doctoral Degree in Clinical Psychology</div>
  <div class="abs deg-item" style="left:252px;top:608px">Masters Degree in Counseling Psychology</div>
  <div class="abs deg-item" style="left:442px;top:591px">Doctoral Internship, Bayview Medical Center</div>
  <div class="abs deg-item" style="left:442px;top:608px">Masters Internship, Harlow Clinic</div>

  <div class="abs section-title" style="left:88px;top:649px">View Video</div>
  <div class="abs rule" style="left:88px;top:668px;width:181px"><b></b></div>
  <div class="abs video" role="img" aria-label="Video still of Dr. Kalvoric"></div>
  <svg class="abs play" width="20" height="20" viewBox="0 0 20 20" aria-hidden="true"><circle cx="10" cy="10" r="8.5" fill="none" stroke="#fff" stroke-width="1.4"/><path d="M8 6v8l6-4z" fill="#fff"/></svg>

  <div class="abs section-title" style="left:293px;top:649px">Quick Inquiry</div>
  <div class="abs rule" style="left:293px;top:668px;width:173px"><b></b></div>
  <div class="abs inq-desc">Lorem ipsum dolor sit amet, consectetuer</div>
  <div class="abs field" style="top:696px">Name</div>
  <div class="abs field" style="top:718px">Email</div>
  <div class="abs field" style="top:740px">Phone</div>
  <div class="abs field" style="top:762px;height:31px">Message</div>
  <div class="abs submit">SUBMIT</div>

  <div class="abs poster" role="img" aria-label="Silver Cedar Tunes radio show poster with Sunday airtime"></div>

  <div class="abs reviews"></div>
  <div class="abs rev-title">Reviews From Former Patients</div>
  <div class="abs rev-rule"><b></b></div>
  <div class="abs portrait rev-photo" role="img" aria-label="Photo of a former patient"></div>
  <p class="abs rev-quote"><span class="qm">“</span> Lorem ipsum dolor sit amet, consectetuer adipiscing elit, sed diam nonummy nibh euismod tincidunt ut laoreet dolore magna aliquam erat volutpat. Ut wisi enim ad minim veniam, quis nostrud exerci tation ullamcorper suscipit lobortis nisl ut aliquip commodo consequat. Duis autem vel eum iriure dolor in hendrerit in vulputate velit esse molestie consequat, vel illum dolore eu feugiat nulla facilisis at vero eros et accumsan et iusto odio dignissimaugue duis dolore te feugait nulla facilisi.</p>
  <div class="abs rev-who">.... Lorem Ispum, Manger</div>
  <a class="abs rev-more"><u>Read more testimonials</u> »</a>
</main>

<footer>
  <div class="abs footer"></div>
  <div class="abs f-title" style="left:88px;top:1039px;width:72px">Quick Links</div>
  <ul class="abs f-links">
    <li>Home</li><li>About Me</li><li>Sessions</li><li>Resources</li><li>BIO</li><li>Customer Reviews</li><li>Contact Me</li>
  </ul>

  <div class="abs f-title" style="left:212px;top:1039px;width:156px">A Portion of All Revenue Is Donated To</div>
  <div class="abs badge-a" role="img" aria-label="Partner charity badge"></div>
  <div class="abs badge-b" role="img" aria-label="Partner charity badge"></div>

  <div class="abs f-title" style="left:423px;top:1039px;width:118px">Contact Details</div>
  <div class="abs c-row" style="left:423px;top:1064px"><b>A:</b>415 Larkin Avenue, Suite 210<br><b></b>Harbor Point, CA 92611</div>
  <div class="abs c-row" style="left:423px;top:1099px"><b>P:</b>949-555-0182</div>
  <div class="abs c-row" style="left:423px;top:1120px"><b>TF:</b>949-555-0182</div>
  <div class="abs c-row" style="left:423px;top:1141px"><b>E:</b>mk@drkalvoric.com</div>

  <div class="abs rating" role="img" aria-label="Five star rating badge on Rivo"></div>
  <div class="abs share">Friendora</div>

  <div class="abs bottom">Copyright © 2016 Dr. Marla J. Kalvoric &nbsp;All rights reserved</div>
</footer>

</body>
</html>
```